Corwin Beacon Lighting - Commercial & Residential Landscape Lighting

Landscape Lighting Services & Design: Create a website for our landscape lighting company. We would like the design to be tailored around this description:
Illuminate with Confidence. Designed with Precision. Installed with Care.
Locally and veteran-owned, we take pride in transforming outdoor spaces through innovative lighting solutions tailored to your vision. From landscape and holiday lighting to permanent installations, our effortless process and expert design deliver breathtaking results and lasting curb appeal. Backed by a lifetime warranty and quarterly service options, our commitment to quality and customer satisfaction is unwavering. Try before you buy and experience your home in a whole new light with our complimentary demo kit — see the stunning effects before you decide.
- Also, add in this information as well; Outdoor Lighting not only beautifies spaces but also significantly enhances safety by illuminating your home or business. Beautifully lit entrances deter potential intruders, making your home a safer place for your loved ones. we also offer quarterly service plans to ensure lighting equipment continues to operate & illuminate effectively throughout the year. Also mention we provide free estimates and we are offering a 10% discount to military, veterans, and first responders.

Target Market(s)

Luxury market

Industry/Entity Type

Landscape Lighting - Residential & Commercial Lighting Services

Coding

Coded - Design and coding required

Number of Pages Required

2 page

Colors
00AB8E
00BBA5
67D7C9
C6EFE9
E9F9F6
59FF00
82FF00
B8FF75
E3FFCB
F4FFEA
FFC000
F8CF3A
FAE287
FDF2CF
FEFAEE

Requirements
Must have
• a lead generation button where people can submit their information for us to reach out to them and schedule their free estimate, homepage, about page, contact page, products and services page, user friendly, easy to navigate, and it also must be engaging and eye popping, as well as appealing to the luxury market. Please use colors; verdent green, dark green, ivory, and sunny yellow. Also, include an about page that references our story; Derek is retired Army and he opened a fitness studio in 2017 with his wife Jolene. He has installed low voltage lighting in every home he lived in and for his friends and family over the years and decided to open his own business because he is passionate about beautifying outdoor landscapes and highlighting a properties full potential, not only in the day but at night as well all while providing safety and security for his clients. Having a deep respect for nature and landscaping, he wants to provide the same care and quality to each of his clients as he has in the fitness industry for decades. He believes small businesses are the back bone of America and he's excited to provide a service that is all to often neglected in the design of a home.
Nice to have
• I would like to have a clear intent and purpose, engaging web design, clear call to action, optimized for search engines, mobile friendy design, security measures, credibility indicators

```html
<!DOCTYPE html>
<html lang="en">
<head>
<meta charset="utf-8">
<title>Corwin Beacon Lighting – Landscape Lighting</title>
<link href="https://fonts.googleapis.com/css2?family=Montserrat:wght@400;500;600;700&display=swap" rel="stylesheet">
<style>
:root{
  --dark:#1d1d1d;
  --orange:#f6a55c;
  --orange-deep:#e48c3f;
  --btn:#f4a258;
  --teal:#19a078;
  --lime:#59ff00;
  --white:#ffffff;
  --ink:#141414;
}
*{margin:0;padding:0;box-sizing:border-box}
html,body{width:1200px;height:4626px;overflow:hidden}
body{position:relative;background:var(--dark);font-family:'Montserrat',sans-serif;color:var(--white)}
.abs{position:absolute}
.layer-photo{z-index:0}
.waves{position:absolute;left:0;top:0;z-index:1}
.content{z-index:2}
.btn{position:absolute;z-index:2;display:flex;align-items:center;justify-content:center;font-weight:700;font-size:14px;letter-spacing:.3px;text-transform:uppercase;border-radius:5px;color:var(--white);background:var(--btn);text-decoration:none}
.title{position:absolute;z-index:2;left:0;width:1200px;text-align:center;font-weight:500;font-size:40px;color:var(--orange);letter-spacing:.5px}

/* header */
.logo{position:absolute;z-index:2;color:var(--orange);font-weight:600;font-size:22px;line-height:26px;letter-spacing:1px}
.nav a{position:absolute;z-index:2;top:35px;font-size:13.5px;font-weight:600;color:var(--white);text-decoration:none}
.nav a.active{color:var(--orange)}
.nav .bar{position:absolute;z-index:2;left:325px;top:0;width:44px;height:5px;background:var(--orange)}

/* hero */
.hero-photo{left:0;top:0;width:1200px;height:700px;background:linear-gradient(180deg,#2b2016 0%,#6b4a27 25%,#8a6a38 45%,#4d6a28 70%,#35521d 100%)}
.hero-head{position:absolute;z-index:2;left:0;top:203px;width:1200px;text-align:center;font-weight:700;font-size:40px;line-height:55px;letter-spacing:.5px}

/* about */
.about-text{position:absolute;z-index:2;left:195px;top:790px;width:810px;text-align:center;font-size:14px;line-height:28.5px}
.about-text .lead{font-size:15.5px}

/* services */
.card{position:absolute;z-index:2;width:330px}
.card .icon{width:68px;height:70px;background:#c9833f;border-radius:4px}
.card h3{font-size:19px;font-weight:500;color:var(--orange);margin-top:26px;line-height:31px}
.card p{font-size:13.5px;line-height:27px;margin-top:6px;padding-left:2px;width:280px}
.card.featured{background:var(--orange-deep);border-radius:5px;padding:22px 30px;height:282px}
.card.featured h3{color:var(--white)}
.card.featured p{width:270px}
.card.featured .icon{background:#f4c08d}
.arrow-btn{position:absolute;z-index:2}

/* demo */
.demo-photo{left:0;top:1500px;width:1200px;height:700px;background:linear-gradient(90deg,#c9b07a 0%,#a98a52 35%,#6e5226 60%,#2d2418 100%)}
.demo{position:absolute;z-index:2;left:111px;top:1720px;width:520px;color:var(--ink)}
.demo h2{font-size:33px;font-weight:600;line-height:44px}
.demo .sub{font-size:21px;line-height:35px;margin-top:8px;font-weight:500}
.demo p{font-size:13px;line-height:28px;white-space:nowrap}

/* beauty */
.ph{position:absolute;z-index:2;border-radius:3px}
.beauty-text{position:absolute;z-index:2;left:621px;top:2328px;width:440px}
.beauty-text h3{font-size:22px;font-weight:500;line-height:35px;white-space:nowrap}
.beauty-text p{font-size:13.5px;line-height:28.5px;margin-top:22px;padding-left:7px;width:420px}

/* discount */
.disc-photo{left:0;top:2800px;width:1200px;height:700px;background:linear-gradient(180deg,#15191a 0%,#232b24 40%,#31432b 70%,#1a2417 100%)}
.disc-head{position:absolute;z-index:2;left:0;top:3068px;width:1200px;text-align:center;font-size:35px;font-weight:600;line-height:50px;letter-spacing:.3px}

/* story */
.story-title{position:absolute;z-index:2;left:111px;top:3568px;font-size:40px;font-weight:500;color:var(--orange)}
.story-text{position:absolute;z-index:2;left:118px;top:3634px;width:410px;font-size:14px;line-height:28.4px}

/* footer */
.foot h4{font-size:20px;font-weight:600;line-height:28px}
.foot{position:absolute;z-index:2}
.foot ul{list-style:none;margin-top:24px}
.foot li{font-size:13.5px;line-height:27.5px}
.contact li{display:flex;gap:10px;align-items:flex-start;line-height:32px;font-size:14px}
.news p{font-size:12.5px;line-height:24px;margin-top:14px}
.news .field{margin-top:18px;width:214px;height:44px;background:var(--white);border-radius:4px;position:relative;display:flex;align-items:center;padding-left:10px;color:#777;font-size:12.5px}
.news .send{position:absolute;right:0;top:0;width:48px;height:44px;background:var(--lime);border-radius:4px;display:flex;align-items:center;justify-content:center}
.rule{position:absolute;z-index:2;left:104px;top:4544px;width:978px;height:1px;background:#555}
.copy{position:absolute;z-index:2;left:0;top:4580px;width:1200px;text-align:center;font-size:13px}
</style>
</head>
<body>

<div class="abs layer-photo hero-photo" role="img" aria-label="Night garden path with glowing lantern lights leading to a lit home"></div>
<div class="abs layer-photo demo-photo" role="img" aria-label="Close-up of a glowing landscape bollard light among plants at dusk"></div>
<div class="abs layer-photo disc-photo" role="img" aria-label="Lit home with a landscaped walkway at night"></div>

<svg class="waves" width="1200" height="4626" viewBox="0 0 1200 4626" aria-hidden="true">
  <rect x="0" y="0" width="1200" height="84" fill="#1b1510" opacity=".85"/>
  <path d="M0 665 Q600 515 1200 665 L1200 1540 Q600 1750 0 1540 Z" fill="#1d1d1d"/>
  <path d="M0 2155 Q600 2025 1200 2155 L1200 2829 Q600 2955 0 2829 Z" fill="#1d1d1d"/>
  <path d="M0 3448 Q600 3304 1200 3448 L1200 4626 L0 4626 Z" fill="#1d1d1d"/>
  <g fill="none" stroke="#f6a55c" stroke-width="10">
    <path d="M0 665 Q600 515 1200 665"/>
    <path d="M0 1540 Q600 1750 1200 1540"/>
    <path d="M0 2155 Q600 2025 1200 2155"/>
    <path d="M0 2829 Q600 2955 1200 2829"/>
    <path d="M0 3448 Q600 3304 1200 3448"/>
    <path d="M0 4077 Q600 4257 1200 4077"/>
  </g>
</svg>

<header>
  <div class="logo" style="left:111px;top:20px;">CORWIN BEACON<br>LIGHTING</div>
  <nav class="nav">
    <span class="bar"></span>
    <a class="active" href="#" style="left:329px">HOME</a>
    <a href="#" style="left:408px">ABOUT US</a>
    <a href="#" style="left:517px">SERVICES</a>
    <a href="#" style="left:618px">PRODUCTS</a>
    <a href="#" style="left:731px">CONTACT US</a>
  </nav>
  <a class="btn" href="#" style="left:867px;top:18px;width:225px;height:47px;font-size:14.5px;">Get Free Estimate</a>
</header>

<section>
  <h1 class="hero-head">ILLUMINATE WITH CONFIDENCE.<br>DESIGNED WITH PRECISION.<br>INSTALLED WITH CARE.</h1>
  <a class="btn" href="#" style="left:440px;top:392px;width:320px;height:44px;background:var(--teal);">Schedule Your Free Estimate</a>
</section>

<section>
  <h2 class="title" style="top:726px;">ABOUT US</h2>
  <div class="about-text">
    <p class="lead">Locally and veteran-owned, we take pride in transforming outdoor spaces through innovative lighting solutions tailored to your vision.</p>
    <p>From landscape and holiday lighting to permanent installations, our effortless process and expert design deliver breathtaking results and lasting curb appeal. Backed by a lifetime warranty and quarterly service options, our commitment to quality and customer satisfaction is unwavering. Try before you buy and experience your home in a whole new light with our complimentary demo kit — see the stunning effects before you decide.</p>
  </div>
  <a class="btn" href="#" style="left:438px;top:994px;width:320px;height:46px;">Schedule Your Free Estimate</a>
</section>

<section>
  <h2 class="title" style="top:1174px;">OUR SERVICES</h2>
  <svg class="arrow-btn" style="left:42px;top:1367px" width="38" height="38" viewBox="0 0 38 38" aria-label="Previous"><circle cx="19" cy="19" r="17" fill="none" stroke="#888" stroke-width="2"/><path d="M22 11 L14 19 L22 27" fill="none" stroke="#888" stroke-width="2.5"/></svg>
  <svg class="arrow-btn" style="left:1110px;top:1367px" width="38" height="38" viewBox="0 0 38 38" aria-label="Next"><circle cx="19" cy="19" r="17" fill="none" stroke="#f6a55c" stroke-width="2"/><path d="M16 11 L24 19 L16 27" fill="none" stroke="#f6a55c" stroke-width="2.5"/></svg>

  <article class="card" style="left:133px;top:1272px;">
    <div class="icon" role="img" aria-label="Holiday lighting icon"></div>
    <h3>Holiday Lighting</h3>
    <p>Lorem Ipsum is simply dummy text of the printing and typesetting industry. Lorem Ipsum has been the industry's</p>
  </article>
  <article class="card featured" style="left:442px;top:1255px;">
    <div class="icon" role="img" aria-label="Architectural light post icon"></div>
    <h3 style="margin-top:22px;">Permanent Architectural Lighting</h3>
    <p>Lorem Ipsum is simply dummy text of the printing and typesetting industry.</p>
    <svg style="margin-top:12px" width="30" height="30" viewBox="0 0 30 30" aria-label="Read more"><circle cx="15" cy="15" r="13" fill="none" stroke="#fff" stroke-width="2"/><path d="M8 15 H21 M16 10 L21 15 L16 20" fill="none" stroke="#fff" stroke-width="2"/></svg>
  </article>
  <article class="card" style="left:808px;top:1272px;">
    <div class="icon" role="img" aria-label="Security lighting icon"></div>
    <h3>Security &amp; Safety Lighting</h3>
    <p>Lorem Ipsum is simply dummy text of the printing and typesetting industry. Lorem Ipsum has been the industry's</p>
  </article>
</section>

<section class="demo">
  <h2>SEE IT BEFORE YOU SAY YES</h2>
  <p class="sub">Experience the magic of expert outdoor<br>lighting—risk-free.</p>
  <p>Try before you buy with our complimentary demo kit and witness<br>the transformation of your home before making a commitment.<br>Let your property shine with confidence, beauty, and security.</p>
</section>
<a class="btn" href="#" style="left:111px;top:1941px;width:419px;height:44px;background:var(--lime);color:var(--ink);">Schedule Your Free Lighting Demo Today</a>

<section>
  <h2 class="title" style="top:2226px;">BEAUTY MEETS SECURITY</h2>
  <div class="ph" style="left:124px;top:2333px;width:219px;height:453px;background:linear-gradient(180deg,#3b4866,#6a5a44 60%,#4c4a52);" role="img" aria-label="Stone house entrance lit at night"></div>
  <div class="ph" style="left:361px;top:2333px;width:219px;height:217px;background:linear-gradient(180deg,#2a2e22,#6c6a55 60%,#8f8c7f);" role="img" aria-label="Lit garden walkway"></div>
  <div class="ph" style="left:361px;top:2566px;width:219px;height:218px;background:linear-gradient(180deg,#1d2230,#4c5146 50%,#2c4a24);" role="img" aria-label="Home with lit front garden at night"></div>
  <div class="beauty-text">
    <h3>Outdoor lighting does more than<br>elevate your curb appeal — it protects<br>what matters most.</h3>
    <p>A thoughtfully illuminated exterior not only showcases your home or business in its best light but also plays a vital role in safety and security. Well-lit entryways, paths, and landscaping help deter potential intruders and create a welcoming environment for your family, guests, or customers.</p>
    <p>To ensure your system performs year-round, we offer quarterly service plans that keep your lighting equipment clean, efficient, and glowing just as brilliantly as day one.</p>
  </div>
  <a class="btn" href="#" style="left:629px;top:2750px;width:192px;height:46px;">Read More</a>
</section>

<section>
  <h2 class="disc-head">WE PROVIDE FREE ESTIMATES AND WE ARE<br>OFFERING A 10% DISCOUNT TO MILITARY,<br>VETERANS, AND FIRST RESPONDERS.</h2>
  <a class="btn" href="#" style="left:499px;top:3242px;width:192px;height:47px;">Contact Us</a>
</section>

<section>
  <h2 class="story-title">OUR STORY</h2>
  <p class="story-text">Derek is retired Army and he opened a fitness studio in 2017 with his wife Jolene. He has installed low voltage lighting in every home he lived in and for his friends and family over the years and decided to open his own business because he is passionate about beautifying outdoor landscapes and highlighting a properties full potential, not only in the day but at night as well all while providing safety and security for his clients. Having a deep respect for nature and landscaping, he wants to provide the same care and quality to each of his clients as he has in the fitness industry for decades. He believes small businesses are the back bone of America and he's excited to provide a service that is all to often neglected in the design of a home.</p>
  <svg class="abs content" style="left:600px;top:3560px" width="470" height="460" viewBox="0 0 470 460">
    <circle cx="242" cy="232" r="212" fill="#f6a55c"/>
    <circle cx="226" cy="230" r="212" fill="#1d1d1d"/>
    <circle cx="224" cy="230" r="206" fill="#2c3a35" role="img" aria-label="Portrait of the company founder in dress uniform"/>
  </svg>
</section>

<footer>
  <div class="logo" style="left:111px;top:4270px;font-size:26px;line-height:32px;">CORWIN BEACON<br>LIGHTING</div>
  <div class="foot" style="left:388px;top:4254px;">
    <h4>MAIN LINKS</h4>
    <ul>
      <li>Home</li><li>Who We Are</li><li>What We Do</li><li>The Science Of Pain</li><li>News In Pain Research</li><li>Innovative Solutions</li><li>Get Involved!</li>
    </ul>
  </div>
  <div class="foot contact" style="left:594px;top:4254px;">
    <h4>CONTACT US</h4>
    <ul style="margin-top:18px;">
      <li><svg width="14" height="14" viewBox="0 0 24 24" style="margin-top:9px"><path fill="#fff" d="M6.6 10.8a15 15 0 0 0 6.6 6.6l2.2-2.2c.3-.3.7-.4 1-.2 1.1.4 2.3.6 3.6.6.6 0 1 .4 1 1V20c0 .6-.4 1-1 1A17 17 0 0 1 3 4c0-.6.4-1 1-1h3.5c.6 0 1 .4 1 1 0 1.3.2 2.5.6 3.6.1.3 0 .7-.2 1z"/></svg>+1 555 010 2288</li>
      <li><svg width="14" height="16" viewBox="0 0 24 28" style="margin-top:8px"><path fill="#fff" d="M12 0a9 9 0 0 0-9 9c0 7 9 19 9 19s9-12 9-19a9 9 0 0 0-9-9zm0 13a4 4 0 1 1 0-8 4 4 0 0 1 0 8z"/></svg><span>418 Ember Lane<br>Suite 12, Glenhaven<br>ST 00000</span></li>
      <li><svg width="16" height="12" viewBox="0 0 24 18" style="margin-top:10px"><rect x="1" y="1" width="22" height="16" fill="#fff"/><path d="M1 1 L12 10 L23 1" fill="none" stroke="#1d1d1d" stroke-width="2"/></svg>info@corwinbeacon.com</li>
    </ul>
  </div>
  <div class="foot news" style="left:871px;top:4254px;width:230px;">
    <h4>SIGN UP TO OUR<br>NEWSLETTER</h4>
    <p>We Will Notify You Of Any<br>Important News</p>
    <div class="field">Your Email Address
      <span class="send"><svg width="22" height="22" viewBox="0 0 24 24"><path d="M2 12 L22 3 L15 22 L11 13 Z M11 13 L22 3" fill="none" stroke="#1d1d1d" stroke-width="1.8" stroke-linejoin="round"/></svg></span>
    </div>
  </div>
  <div class="rule"></div>
  <p class="copy">© 2025 Corwin Beacon &nbsp;| All Rights Reserved</p>
</footer>

</body>
</html>
```